Business card design for my company.
I would like the card's background colour to be black. You can also see our web site to get an idea of our brand. https://www.tmwhomecrafting.com.au/
- Name
- Email

```html
<!DOCTYPE html>
<html lang="en">
<head>
<meta charset="utf-8">
<title>TMW Home Crafting – Business Card</title>
<link href="https://fonts.googleapis.com/css2?family=Arimo:wght@400;700&display=swap" rel="stylesheet">
<style>
  :root {
    --backdrop: #e4e4e4;
    --card-dark: #303030;
    --brand-green: #0b9645;
    --emboss-green: #087a37;
    --text-light: #ffffff;
    --divider: #6a6a6a;
  }
  * { margin: 0; padding: 0; box-sizing: border-box; }
  html, body {
    width: 1200px; height: 1200px; overflow: hidden;
    background: var(--backdrop);
    font-family: "Arimo", Arial, sans-serif;
  }
  .canvas { position: relative; width: 1200px; height: 1200px; }

  .card {
    position: absolute;
    width: 688px; height: 393px;
    overflow: hidden;
  }
  .card-front { left: 266px; top: 158px; background: var(--card-dark); }
  .card-back  { left: 262px; top: 653px; background: var(--brand-green); }

  .brand-lockup {
    position: absolute;
    display: flex; align-items: center; justify-content: center; gap: 10px;
    font-weight: 700; white-space: nowrap;
  }
  .brand-mark { width: 18px; height: 18px; flex: none; }
  .card-front .brand-lockup {
    left: 40px; width: 300px; top: 178px; height: 30px;
    font-size: 22px; color: var(--text-light);
  }
  .card-front .brand-mark { background: var(--brand-green); }
  .card-back .brand-lockup {
    left: 0; right: 0; top: 172px;
    font-size: 40px; color: var(--emboss-green); gap: 12px;
  }
  .card-back .brand-mark { width: 30px; height: 30px; background: var(--emboss-green); }

  .divider {
    position: absolute; left: 359px; top: 90px;
    width: 1px; height: 196px; background: var(--divider);
  }

  .contact-block { position: absolute; left: 391px; top: 96px; color: var(--text-light); }
  .person-name { font-size: 27px; font-weight: 700; color: var(--brand-green); line-height: 1; letter-spacing: 0.3px; }
  .person-title { font-size: 15px; margin-top: 4px; }
  .address { font-size: 15px; line-height: 21px; margin-top: 16px; }
  .contact-list { list-style: none; margin-top: 12px; }
  .contact-list li { display: flex; align-items: center; gap: 11px; font-size: 15px; height: 20.5px; }
  .contact-list svg { width: 14px; height: 14px; fill: var(--brand-green); flex: none; }

  .footer-band { position: absolute; left: 0; bottom: 0; width: 688px; height: 32px; }
  .web-address {
    position: absolute; right: 22px; bottom: 8px;
    font-size: 13px; letter-spacing: 0.6px; color: var(--text-light);
    white-space: nowrap;
  }
</style>
</head>
<body>
<main class="canvas">

  <section class="card card-front" aria-label="Business card front">
    <div class="brand-lockup"><span class="brand-mark"></span>TMW Home Crafting</div>
    <div class="divider"></div>

    <div class="contact-block">
      <p class="person-name">DANIEL REEVE</p>
      <p class="person-title">President</p>
      <p class="address">214 Harbour Crest Road<br>Geelong, VIC 3220</p>
      <ul class="contact-list">
        <li>
          <svg viewBox="0 0 24 24" aria-hidden="true"><path d="M6.6 10.8a15.1 15.1 0 0 0 6.6 6.6l2.2-2.2a1 1 0 0 1 1-.25 11.4 11.4 0 0 0 3.6.57 1 1 0 0 1 1 1V20a1 1 0 0 1-1 1A17 17 0 0 1 3 4a1 1 0 0 1 1-1h3.5a1 1 0 0 1 1 1c0 1.25.2 2.450.57 3.57a1 1 0 0 1-.25 1z"/></svg>
          03-5521-4870
        </li>
        <li>
          <svg viewBox="0 0 24 24" aria-hidden="true"><path d="M7 1h10a2 2 0 0 1 2 2v18a2 2 0 0 1-2 2H7a2 2 0 0 1-2-2V3a2 2 0 0 1 2-2zm0 3v15h10V4zm5 16.2a1 1 0 1 0 0 .01z"/></svg>
          0412-639-205
        </li>
        <li>
          <svg viewBox="0 0 24 24" aria-hidden="true"><path d="M2 5h20v14H2zm2 2v.5l8 5 8-5V7zm0 2.9V17h16V9.9l-8 5z"/></svg>
          info@tmwhomecrafting.com.au
        </li>
      </ul>
    </div>

    <svg class="footer-band" viewBox="0 0 688 32" aria-hidden="true">
      <polygon points="0,0 438,0 430,14 0,14" fill="#ffffff"/>
      <polygon points="0,19 436,19 446,0 688,0 688,32 0,32" fill="#0b9645"/>
    </svg>
    <span class="web-address">www.tmwhomecrafting.com.au</span>
  </section>

  <section class="card card-back" aria-label="Business card back">
    <div class="brand-lockup"><span class="brand-mark"></span>TMW Home Crafting</div>
  </section>

</main>
</body>
</html>
```